Kelvaro.ch is looking for business card letterhead and envelope C5 with WOW effect

We need a strong business card for our company Kelvaro.ch, logo is available. You want a black or dark background on which the logo Stark r% 26 # 252; appears. Letterhead and envelope in C5 format should be in a similar design, but does not have to be We need a strong business card for our company Kelvaro.ch, logo is available. A black or dark background is desired, on which the logo Stark comes across. The letterhead and the envelope in C5 format should have a similar design.

Target Market(s)

Private customers as well as entrepreneurs

Contact Information for Business Card

E-mail: info@kelvaro-example.ch
Web.www.Kelvaro-example.ch
Tel: +41 ( 0 ) 79 482 6037
Adresse:
Lindenweg 14
9406 Tarnbach

Hier kann man Icons verwenden für Email,Tel und Adressse

Font styles to use
Other font styles liked:
• Dubai,bold

Colors

Designer to choose colors to be used in the design.

Requirements
Must have
• WOW effect
Nice to have
• R% 26 # 252; back business card with our service listings. - VEHICLE LABELING - SHOP WINDOW LABELING - STICKERS AND MUCH MORE ... in red color

```html
<!DOCTYPE html>
<html lang="en">
<head>
<meta charset="utf-8">
<title>Kelvaro.ch – Business Card</title>
<link href="https://fonts.googleapis.com/css2?family=Ubuntu:wght@400;500;700&display=swap" rel="stylesheet">
<style>
  :root {
    --stage: #141414;
    --card: #1f1f1f;
    --card-edge: #262626;
    --white: #f4f4f4;
    --grey: #b9b9b9;
    --yellow: #f5c518;
    --red: #e0242b;
    --hex-light: #5a5a5a;
    --hex-dark: #181818;
  }
  * { margin: 0; padding: 0; box-sizing: border-box; }
  html, body {
    width: 1200px; height: 900px; overflow: hidden;
    background: var(--stage);
    font-family: "Ubuntu", sans-serif;
  }
  .canvas {
    position: relative; width: 1200px; height: 900px;
    display: flex; flex-direction: column; align-items: center; justify-content: center; gap: 40px;
  }
  .card {
    position: relative; width: 600px; height: 388px;
    background: linear-gradient(135deg, var(--card-edge), var(--card));
    border-bottom: 5px solid var(--yellow);
    overflow: hidden;
  }
  .wordmark {
    font-weight: 700; color: var(--white); letter-spacing: 1px; text-transform: uppercase;
  }
  /* back side */
  .back .pattern-area {
    position: absolute; left: 150px; top: 70px; width: 140px; height: 180px;
    background: radial-gradient(ellipse at 60% 60%, #3a3a3a, var(--hex-dark) 75%);
    border-radius: 8px;
  }
  .back .wordmark {
    position: absolute; left: 310px; top: 138px; font-size: 34px; color: var(--grey);
  }
  .services {
    position: absolute; right: 60px; top: 232px; list-style: none; text-align: right;
  }
  .services li {
    color: var(--white); font-size: 13px; line-height: 22px; text-transform: uppercase;
    display: flex; align-items: center; justify-content: flex-end; gap: 10px;
  }
  .services li::after {
    content: ""; width: 8px; height: 8px; border: 2px solid var(--red); border-radius: 50%;
  }
  /* front side */
  .front .wordmark { position: absolute; left: 44px; top: 38px; font-size: 34px; }
  .front .pattern-area {
    position: absolute; right: 36px; top: 100px; width: 230px; height: 260px;
    background: radial-gradient(ellipse at 50% 35%, var(--hex-light), var(--hex-dark) 75%);
    border-radius: 10px; opacity: .85;
  }
  .person { position: absolute; left: 60px; top: 150px; }
  .person-name { font-size: 22px; font-weight: 700; letter-spacing: 2.5px; color: var(--white); }
  .person-name .surname { color: var(--yellow); }
  .person-role { font-size: 14px; color: var(--white); letter-spacing: 1px; margin-top: 2px; }
  .divider { width: 36px; height: 1px; background: var(--yellow); margin: 14px 0 16px; }
  .contacts { list-style: none; }
  .contacts li {
    display: flex; align-items: center; gap: 10px;
    font-size: 15px; color: var(--white); line-height: 26px; letter-spacing: .5px;
  }
  .contacts svg { width: 13px; height: 13px; flex: none; }
  .address { font-size: 15px; color: var(--white); letter-spacing: .8px; margin-top: 10px; }
</style>
</head>
<body>
<main class="canvas">
  <section class="card back">
    <div class="pattern-area" role="img" aria-label="Cluster of embossed hexagon shapes"></div>
    <h1 class="wordmark">Kelvaro.ch</h1>
    <ul class="services">
      <li>Vehicle labeling</li>
      <li>Shop window labeling</li>
      <li>Stickers and much more</li>
    </ul>
  </section>

  <section class="card front">
    <h2 class="wordmark">Kelvaro.ch</h2>
    <div class="pattern-area" role="img" aria-label="Large cluster of glossy hexagon shapes"></div>
    <div class="person">
      <p class="person-name">LUKAS <span class="surname">BRENNER</span></p>
      <p class="person-role">Director</p>
      <div class="divider"></div>
      <ul class="contacts">
        <li>
          <svg viewBox="0 0 16 16" aria-hidden="true"><path fill="var(--yellow)" d="M4 1l3 3-2 2c1 2 3 4 5 5l2-2 3 3-2 3C7 15 1 9 1 3z"/></svg>
          +41 ( 0 ) 79 482 6037
        </li>
        <li>
          <svg viewBox="0 0 16 16" aria-hidden="true"><rect x="1" y="3" width="14" height="10" fill="none" stroke="var(--yellow)" stroke-width="1.5"/><path d="M1 3l7 6 7-6" fill="none" stroke="var(--yellow)" stroke-width="1.5"/></svg>
          info@kelvaro-example.ch
        </li>
        <li>
          <svg viewBox="0 0 16 16" aria-hidden="true"><circle cx="8" cy="8" r="6.5" fill="none" stroke="var(--yellow)" stroke-width="1.5"/><ellipse cx="8" cy="8" rx="3" ry="6.5" fill="none" stroke="var(--yellow)" stroke-width="1.2"/><path d="M1.5 8h13M2.5 5h11M2.5 11h11" stroke="var(--yellow)" stroke-width="1"/></svg>
          www.Kelvaro-example.ch
        </li>
      </ul>
      <p class="address">Lindenweg 14 9406 Tarnbach</p>
    </div>
  </section>
</main>
</body>
</html>
```